Local Roofing/Construction company business needs new biz card design

We need a new business card design, current cards are from the start of this operation and generic at best. We are a local Construction Company (General Contractor) with a majority of our work originating from insurance claims-exterior finish work is the main focus (Roofs-Siding-Gutters etc). Heavily involved with homeowners and the low ball offers they receive from insurance company's after a insurable event takes place. I have attached some of our original logo file(s) below.

```html
<!DOCTYPE html>
<html lang="en">
<head>
<meta charset="utf-8">
<title>Harbrook Construction – Business Card</title>
<link rel="stylesheet" href="https://fonts.googleapis.com/css2?family=Montserrat:wght@400;500;700&display=swap">
<style>
  :root {
    --brand-green: #2fd67a;
    --brand-green-deep: #27c56d;
    --ink-navy: #1f2a5a;
    --ink-grey: #3d3d3d;
    --card-white: #ffffff;
    --backdrop: #d9d9d9;
  }
  * { box-sizing: border-box; margin: 0; padding: 0; }
  html, body {
    width: 1200px; height: 800px; overflow: hidden;
    background: var(--backdrop);
    font-family: 'Montserrat', sans-serif;
  }
  .canvas { position: relative; width: 1200px; height: 800px; }

  .card {
    position: absolute; width: 540px; height: 310px;
    box-shadow: 0 14px 30px rgba(0,0,0,.22);
  }
  .card--front {
    left: 60px; top: 110px;
    background: var(--card-white);
    border-bottom: 3px solid var(--brand-green);
    display: flex; align-items: center;
  }
  .card--back {
    left: 600px; top: 380px;
    background: var(--brand-green);
    display: flex; align-items: center; justify-content: center;
  }

  .brand-mark {
    width: 250px; display: flex; align-items: center; justify-content: center;
  }
  .brand-name {
    font-weight: 700; font-size: 22px; letter-spacing: .06em;
    text-transform: uppercase; line-height: 1.15; text-align: center;
    color: var(--brand-green);
  }
  .card--back .brand-name { color: var(--card-white); font-size: 26px; }

  .divider {
    width: 1.5px; height: 170px; background: var(--brand-green);
  }

  .contact {
    padding-left: 26px; text-transform: uppercase; color: var(--ink-grey);
  }
  .contact__name {
    font-weight: 700; font-size: 19px; color: var(--brand-green); letter-spacing: .02em;
  }
  .contact__role {
    font-weight: 500; font-size: 12.5px; color: var(--ink-navy); margin-bottom: 16px; letter-spacing: .03em;
  }
  .contact__list { list-style: none; margin-bottom: 16px; }
  .contact__item {
    display: flex; align-items: center; gap: 7px;
    font-size: 11.5px; line-height: 1.55; letter-spacing: .03em;
  }
  .contact__item svg { width: 11px; height: 11px; flex: none; }
  .contact__address { font-size: 11.5px; line-height: 1.5; letter-spacing: .03em; }

  .back-pattern {
    position: absolute; inset: 0;
    background: linear-gradient(135deg, var(--brand-green) 0%, var(--brand-green-deep) 100%);
  }
  .back-badge {
    position: relative; display: flex; align-items: center; gap: 12px;
  }
  .back-badge__square {
    width: 18px; height: 18px; background: var(--card-white);
  }
</style>
</head>
<body>
<main class="canvas">

  <section class="card card--front" aria-label="Business card front">
    <div class="brand-mark">
      <span class="brand-name">Harbrook<br>Construction</span>
    </div>
    <div class="divider"></div>
    <div class="contact">
      <p class="contact__name">Daniel Reyes</p>
      <p class="contact__role">Managing Director</p>
      <ul class="contact__list">
        <li class="contact__item">
          <svg viewBox="0 0 24 24" aria-hidden="true"><path fill="#2fd67a" d="M6.6 10.8a15.1 15.1 0 0 0 6.6 6.6l2.2-2.2a1 1 0 0 1 1-.25 11.4 11.4 0 0 0 3.6.57 1 1 0 0 1 1 1V20a1 1 0 0 1-1 1A17 17 0 0 1 3 4a1 1 0 0 1 1-1h3.5a1 1 0 0 1 1 1c0 1.25.2 2.45.57 3.57a1 1 0 0 1-.25 1z"/></svg>
          055-210 347 862
        </li>
        <li class="contact__item">
          <svg viewBox="0 0 24 24" aria-hidden="true"><rect x="2" y="5" width="20" height="14" rx="1.5" fill="#2fd67a"/><path d="M2.5 6l9.5 7 9.5-7" fill="none" stroke="#fff" stroke-width="1.8"/></svg>
          hello@harbrookbuild.com
        </li>
        <li class="contact__item">
          <svg viewBox="0 0 24 24" aria-hidden="true"><circle cx="12" cy="12" r="10" fill="#2fd67a"/><path d="M2 12h20M12 2c3 3 3 17 0 20M12 2c-3 3-3 17 0 20" fill="none" stroke="#fff" stroke-width="1.4"/></svg>
          www.harbrookbuild.com
        </li>
      </ul>
      <p class="contact__address">88, Millstone Road<br>30417, Eastvale</p>
    </div>
  </section>

  <section class="card card--back" aria-label="Business card back">
    <div class="back-pattern" role="img" aria-label="Repeating faint brand pattern tiled across the green background"></div>
    <div class="back-badge">
      <span class="back-badge__square"></span>
      <span class="brand-name">Harbrook<br>Construction</span>
    </div>
  </section>

</main>
</body>
</html>
```